VORELT B2B portal design
Fantastic design work, top communication and fast design changes! Many thanks,Jarek & Lutz from VORELT
Zielgruppe
We are a B2B Cloud Services StartUp that creates B2B logistics & supply chain processes between customer and its suppliers.
Aufgabenstellung
We need a modern responsive able design, that should consider that we are NOT presenting goods or clothes or similar on the portal pages but we show mainly data grids, kpi dashboards, forms, and setting panels to our customer and their suppliers.
The design must be clean and straight not to distract people from the important information in these data grids, kpi dashboards, forms, and settings panels.
We need our logo perfectly embedded and the pages coloured around from grey to blue.
The Designer must be able to deliver a design and transfer it to a highly responsive HTML (5) template (without technical content or further functionality). This our programmers will implement afterwards in .Net.
We need in total 3 page templates:
1. Login Page
2. Main Page with overview over the following services text (each one shown in one tile)
"ZMS (Time Frame Management)"
"DMS (Document Management)"
"REMS (Reporting Management)"
-> Note: At the end we will have up to 12 or more tiles (services) so the design should be additive
3. Data grid (e.g. list of customers)/form (e.g. customer registration form) page to show some data grid with database data
See samples for each page enclosed!!

```html
<!DOCTYPE html>
<html lang="en">
<head>
<meta charset="utf-8">
<title>VORELT Portal – Services</title>
<link href="https://fonts.googleapis.com/css2?family=Ubuntu:wght@400;500;700&family=Ubuntu+Condensed&family=Open+Sans:wght@400;600&display=swap" rel="stylesheet">
<style>
:root{
  --navy:#062a47;
  --navy-active:#0b3350;
  --navy-sub:#0e3a58;
  --navy-sub-hi:#174a6b;
  --side-bg:#e3e7ea;
  --side-line:#c9d0d6;
  --content-bg:#f5f7f9;
  --ink:#1f3346;
  --ink-soft:#555e66;
  --grid-line:#c9ced3;
  --grid-head:#e4e8eb;
  --row-alt:#eaf5fa;
  --white:#ffffff;
}
*{box-sizing:border-box;margin:0;padding:0}
html,body{width:1200px;height:1020px;overflow:hidden}
body{position:relative;background:var(--content-bg);font-family:"Ubuntu",sans-serif;color:var(--ink)}

.topbar{position:absolute;left:0;top:0;width:1200px;height:72px;background:var(--navy);color:var(--white)}
.user{position:absolute;right:110px;top:15px;text-align:right}
.user-name{font-size:20px;font-weight:500}
.user-mail{font-size:14px;margin-top:1px}
.avatar{position:absolute;right:41px;top:10px;width:53px;height:53px;border-radius:50%;background:radial-gradient(circle at 50% 40%,#8a8580,#3c3a38)}
.user-caret{position:absolute;right:15px;top:31px}

.sidebar{position:absolute;left:0;top:72px;width:328px;height:886px;background:var(--side-bg)}
.brand{height:218px;background:linear-gradient(135deg,#cfd4d8 0%,#e4e7ea 45%,#d5d9dc 100%);display:flex;align-items:center;padding-left:24px;gap:14px}
.brand-dot{width:22px;height:22px;border-radius:50%;background:var(--navy)}
.brand-name{font-size:56px;font-weight:700;color:var(--navy);letter-spacing:1px}
.menu{list-style:none}
.menu-item{height:61px;display:flex;align-items:center;padding-left:20px;gap:10px;border-bottom:1px solid var(--side-line);font-family:"Ubuntu Condensed",sans-serif;font-size:21px;color:var(--ink)}
.menu-item svg{width:28px;height:28px;flex:none}
.menu-item.is-open{background:var(--navy-active);color:var(--white);border-bottom:none;position:relative}
.menu-item.is-open .chev{position:absolute;right:18px;top:24px;width:14px;height:14px}
.submenu{list-style:none;background:var(--navy-sub);padding-bottom:12px}
.submenu li{height:61px;display:flex;align-items:center;padding-left:56px;color:var(--white);font-size:19px;border-bottom:1px solid #0a3049}
.submenu li.is-current{background:var(--navy-sub-hi)}

.main{position:absolute;left:352px;top:72px;width:830px}
.section-title{font-size:25px;font-weight:400;color:var(--ink)}
.grid-title{margin-top:42px}
.table-title{margin-top:68px}

table{border-collapse:collapse;background:var(--white)}
th{background:var(--grid-head);font-weight:400;font-size:17px;text-align:left;padding-left:13px;border:1px solid var(--grid-line);color:var(--ink)}
td{font-family:"Open Sans",sans-serif;font-size:14px;color:var(--ink-soft);padding-left:13px;border:1px solid var(--grid-line)}
.data-grid{width:830px;margin-top:16px;table-layout:fixed}
.data-grid th{height:39px}
.data-grid td{height:41px}
.data-grid td.center,.data-grid th.center{text-align:center;padding-left:0}
.check{display:inline-block;width:15px;height:15px;border:1px solid #7d858c;background:linear-gradient(#fff,#e6e9ec);vertical-align:middle}
.data-grid td.batch,.data-grid th.batch{padding-left:38px}

.pager-bar{width:830px;height:59px;border:1px solid var(--grid-line);border-top:none;background:var(--content-bg);position:relative}
.show{position:absolute;left:21px;top:17px;font-size:17px;display:flex;align-items:center;gap:6px}
.select{width:80px;height:34px;border:1px solid var(--grid-line);background:var(--white);position:relative;font-family:"Open Sans",sans-serif;font-size:14px;padding:9px 0 0 16px}
.select-btn{position:absolute;right:0;top:0;width:19px;height:32px;border:1px solid #555;background:#e6e6e6}
.select-btn:after{content:"";position:absolute;left:5px;top:13px;border:4px solid transparent;border-top:5px solid #222}
.pages{position:absolute;right:12px;top:10px;height:37px;display:flex;align-items:center;background:var(--white);font-size:14px}
.page-btn{height:37px;padding:0 13px;background:var(--navy);color:var(--white);font-weight:700;font-size:14px;display:flex;align-items:center;border-radius:3px}
.page-list{display:flex;align-items:center;height:37px;padding:0 10px 0 30px}
.page-list span{padding:0 5px}
.page-list .is-current{background:#b7bcc0;color:var(--white);height:37px;display:flex;align-items:center;padding:0 7px;margin-right:3px}

.simple-table{margin-top:16px;table-layout:fixed;width:417px}
.simple-table th{height:39px}
.simple-table td{height:36px}
.simple-table tr:nth-child(even) td{background:var(--row-alt)}

.footer{position:absolute;left:0;top:958px;width:1200px;height:62px;background:var(--white);border-top:2px solid #e6e9ec;font-family:"Ubuntu Condensed",sans-serif;font-size:16px;color:var(--ink)}
.copyright{position:absolute;left:14px;top:21px}
.footer-links{position:absolute;right:22px;top:21px;word-spacing:2px}
</style>
</head>
<body>

<header class="topbar">
  <div class="user">
    <div class="user-name">Nils Brandt</div>
    <div class="user-mail">nils_brandt@postfeld.net</div>
  </div>
  <div class="avatar" role="img" aria-label="User profile photo"></div>
  <svg class="user-caret" width="10" height="8" viewBox="0 0 10 8"><path d="M0 0h10L5 7z" fill="#fff"/></svg>
</header>

<aside class="sidebar">
  <div class="brand">
    <span class="brand-dot"></span>
    <span class="brand-name">VORELT</span>
  </div>
  <ul class="menu">
    <li class="menu-item">
      <svg viewBox="0 0 28 28"><circle cx="14" cy="14" r="11" fill="none" stroke="#1f3346" stroke-width="2"/><ellipse cx="14" cy="14" rx="5" ry="11" fill="none" stroke="#1f3346" stroke-width="1.5"/><rect x="2" y="10" width="24" height="8" fill="#e3e7ea"/><text x="14" y="17" font-size="7" font-weight="700" text-anchor="middle" fill="#1f3346" font-family="Ubuntu,sans-serif">NEWS</text></svg>My News</li>
    <li class="menu-item">
      <svg viewBox="0 0 28 28"><circle cx="11" cy="8" r="6" fill="#1f3346"/><path d="M0 26c0-8 5-12 11-12s9 3 10 6v6z" fill="#1f3346"/><circle cx="22" cy="21" r="5" fill="#1f3346"/><circle cx="22" cy="21" r="2" fill="#e3e7ea"/></svg>My User Settings</li>
    <li class="menu-item">
      <svg viewBox="0 0 28 28"><circle cx="10" cy="10" r="7" fill="none" stroke="#1f3346" stroke-width="5" stroke-dasharray="3 2.5"/><circle cx="10" cy="10" r="5" fill="#1f3346"/><circle cx="10" cy="10" r="2" fill="#e3e7ea"/><circle cx="21" cy="21" r="4.5" fill="none" stroke="#1f3346" stroke-width="4" stroke-dasharray="2.5 2"/><circle cx="21" cy="21" r="1.5" fill="#e3e7ea"/></svg>Company Settings</li>
    <li class="menu-item">
      <svg viewBox="0 0 28 28"><path d="M4 24L17 11" stroke="#1f3346" stroke-width="4" stroke-linecap="round"/><path d="M15 5a6 6 0 0 0 8 8l-3-1-3-3-1-3z" fill="#1f3346"/><path d="M6 4l4 4-2 2-4-4z M10 9l12 13-2 2L8 11z" fill="#1f3346"/></svg>Configuration</li>
    <li class="menu-item is-open">
      <svg viewBox="0 0 28 28" fill="#fff"><rect x="2" y="4" width="5" height="5"/><rect x="9" y="4" width="17" height="5"/><rect x="2" y="11" width="5" height="5"/><rect x="9" y="11" width="17" height="5"/><rect x="2" y="18" width="5" height="5"/><rect x="9" y="18" width="17" height="5"/></svg>Services
      <svg class="chev" viewBox="0 0 14 14"><path d="M2 4l5 5 5-5" fill="none" stroke="#fff" stroke-width="2"/></svg>
    </li>
  </ul>
  <ul class="submenu">
    <li class="is-current">TMS</li>
    <li>DMS</li>
    <li>REMS</li>
  </ul>
  <ul class="menu">
    <li class="menu-item">
      <svg viewBox="0 0 28 28"><ellipse cx="15" cy="12" rx="11" ry="8" fill="#1f3346"/><path d="M6 16l-3 7 8-4z" fill="#1f3346"/></svg>Communication</li>
    <li class="menu-item">
      <svg viewBox="0 0 28 28"><path d="M13 6H5v17h17v-8" fill="none" stroke="#1f3346" stroke-width="3"/><path d="M11 17L23 5M16 4h8v8" fill="none" stroke="#1f3346" stroke-width="3"/></svg>Logout</li>
  </ul>
</aside>

<main class="main">
  <h2 class="section-title grid-title">Grid Styling</h2>
  <table class="data-grid">
    <colgroup><col style="width:48px"><col style="width:120px"><col style="width:120px"><col style="width:204px"><col style="width:108px"><col></colgroup>
    <thead><tr><th class="center"><span class="check"></span></th><th>Record</th><th>Batch ID</th><th>Keyword</th><th>Status</th><th>Reason</th></tr></thead>
    <tbody>
      <tr><td class="center"><span class="check"></span></td><td>Danish</td><td class="batch">Yes</td><td>Some Dummy Text</td><td>Rejected</td><td>Policy Error: (adult)</td></tr>
      <tr><td class="center"><span class="check"></span></td><td>Danish</td><td class="batch">Yes</td><td>Some Dummy Text</td><td>Rejected</td><td>Policy Error: (adult)</td></tr>
      <tr><td class="center"><span class="check"></span></td><td>Danish</td><td class="batch">Yes</td><td>Some Dummy Text</td><td>Rejected</td><td>Policy Error: (adult)</td></tr>
      <tr><td class="center"><span class="check"></span></td><td>Danish</td><td class="batch">Yes</td><td>Some Dummy Text</td><td>Rejected</td><td>Policy Error: (adult)</td></tr>
    </tbody>
  </table>
  <div class="pager-bar">
    <div class="show">Show <span class="select">10<span class="select-btn"></span></span> entries</div>
    <div class="pages">
      <span class="page-btn">FIRST</span>
      <span class="page-list"><span class="is-current">1</span><span>2</span><span>3</span><span>4</span><span>5</span><span>6</span><span>7</span><span>8</span><span>9</span><span>10</span><span>....</span><span>100</span></span>
      <span class="page-btn">LAST</span>
    </div>
  </div>

  <h2 class="section-title table-title">Table Styling</h2>
  <table class="simple-table">
    <colgroup><col style="width:72px"><col style="width:204px"><col></colgroup>
    <thead><tr><th>ID</th><th>Name</th><th>Approved</th></tr></thead>
    <tbody>
      <tr><td>201</td><td>Danish</td><td>Yes</td></tr>
      <tr><td>202</td><td>Noman</td><td>No</td></tr>
      <tr><td>203</td><td>Raghib</td><td>Yes</td></tr>
      <tr><td>204</td><td>Ijaz</td><td>No</td></tr>
    </tbody>
  </table>
</main>

<footer class="footer">
  <span class="copyright">© 2016 VORELT. All rights reserved.</span>
  <span class="footer-links">Help / Disclaimer / Contact</span>
</footer>

</body>
</html>
```